Diverse, up-scale salon needs eye-catching, unique business cards.

We are looking for a unique business card design for our stylist but that can also be multi functional and used for appointment reminder and referrals. I will need a design in a format that I can modify names and titles going forward. In the past we have had a dark background with the logo on one side, and stylist and contact information on the other but we are open to all ideas. I have included our mission statement as well as branded colors below. The statement doesn't need to go on the card, it's just a reference for target market. We need space for the stylists name, title, instagram handle and then the salons phone number, website and address. I am also open to adding a spot for a qr code linked to the stylist instagram or the salon booking link.

primary brand colors:
#333333 #233415 #36502a #93874a #000000
Mission statement:
Vessolin Hair Studio, a high-end salon located in the lively Downtown Farmington, Michigan, is committed to providing exceptional services in a welcoming and relaxed environment to meet the needs of our diverse clientele.
Our salon specializes in contemporary custom haircuts, coloring, extensions, and barbering and beard grooming services. Our team of skilled stylists is passionate and inventive in their hair styling techniques. At the heart of our salon are values centered on quality, innovation, creativity, and above all, comfort. These core values are evident in every appointment across our customizable array of services.
Our goal is to establish a benchmark for exceptional hair care for every human.
Website: www.vessolinhairstudio.example
instagram: @vessolinhairstudio
address: 41782 Pelham Crest Rd, Farmington MI
phone: 248-613-4087

Industry/Entity Type

Hair Salon

Contact Information for Business Card

Stylist name, title, phone, instagram, website, address, (optional qr code)

Requirements
Should not have
• Does not need mission statement on the card.

```html
<!DOCTYPE html>
<html lang="en">
<head>
<meta charset="utf-8">
<title>Vessolin Hair Studio – Business Card</title>
<link rel="stylesheet" href="https://fonts.googleapis.com/css2?family=Cinzel:wght@500&family=Montserrat:wght@400;600&display=swap">
<style>
  :root {
    --backdrop: #3a3a3a;
    --card: #111111;
    --gold: #93874a;
    --white: #f2f2f2;
    --silver: #9a9a9a;
  }
  * { margin: 0; padding: 0; box-sizing: border-box; }
  html, body { width: 1200px; height: 801px; overflow: hidden; }
  body {
    background: var(--backdrop);
    font-family: "Montserrat", sans-serif;
    position: relative;
  }
  .card {
    position: absolute;
    top: 246px;
    width: 540px;
    height: 309px;
    background: var(--card);
    border: 2px solid var(--gold);
    box-shadow: 0 14px 30px rgba(0,0,0,.35);
  }
  .card--front { left: 40px; }
  .card--back { left: 620px; display: flex; align-items: center; justify-content: center; }

  .brand-name {
    position: absolute;
    top: 62px;
    right: 34px;
    font-family: "Montserrat", sans-serif;
    font-weight: 600;
    font-size: 13px;
    letter-spacing: 1.5px;
    color: var(--gold);
    text-transform: uppercase;
  }

  .stylist { position: absolute; left: 34px; top: 128px; }
  .stylist__name {
    font-family: "Cinzel", serif;
    font-weight: 500;
    font-size: 24px;
    color: var(--gold);
    letter-spacing: 1px;
    line-height: 1;
  }
  .stylist__title { font-size: 14px; color: var(--white); margin-top: 4px; }

  .divider {
    position: absolute;
    left: 34px; right: 34px; top: 190px;
    height: 1px;
    background: var(--gold);
  }

  .contact-list {
    position: absolute; left: 34px; top: 204px;
    list-style: none;
  }
  .contact-list li {
    display: flex; align-items: center; gap: 8px;
    font-size: 13px; color: var(--white);
    height: 22px;
  }
  .contact-list svg { width: 11px; height: 11px; flex: none; }
  .contact-list__at {
    width: 11px; flex: none;
    font-size: 12px; font-weight: 600; line-height: 1;
    color: var(--gold); text-align: center;
  }

  .address {
    position: absolute; right: 34px; top: 204px;
    text-align: right;
    font-size: 13px; color: var(--white);
    line-height: 22px;
    font-style: normal;
  }

  .back-name {
    font-family: "Montserrat", sans-serif;
    font-weight: 600;
    font-size: 24px;
    letter-spacing: 3px;
    color: var(--silver);
    text-transform: uppercase;
  }
</style>
</head>
<body>
  <section class="card card--front">
    <p class="brand-name">Vessolin Hair Studio</p>

    <div class="stylist">
      <p class="stylist__name">MARISOL</p>
      <p class="stylist__title">President</p>
    </div>

    <div class="divider"></div>

    <ul class="contact-list">
      <li>
        <svg viewBox="0 0 12 12"><path d="M2.5 1 L4.5 1 L5.3 3.4 L4 4.4 Q5 6.8 7.6 8 L8.6 6.7 L11 7.5 L11 9.5 Q11 11 9.5 11 Q1 10.2 1 2.5 Q1 1 2.5 1 Z" fill="var(--gold)"/></svg>
        248-613-4087
      </li>
      <li>
        <span class="contact-list__at">@</span>
        @vessolinhairstudio
      </li>
      <li>
        <svg viewBox="0 0 12 12"><circle cx="6" cy="6" r="5" fill="none" stroke="var(--gold)" stroke-width="1.2"/><ellipse cx="6" cy="6" rx="2.2" ry="5" fill="none" stroke="var(--gold)" stroke-width="1"/><line x1="1" y1="6" x2="11" y2="6" stroke="var(--gold)" stroke-width="1"/></svg>
        www.vessolinhairstudio.example
      </li>
    </ul>

    <address class="address">
      41782 Pelham Crest Rd<br>Farmington MI
    </address>
  </section>

  <section class="card card--back">
    <p class="back-name">Vessolin Hair Studio</p>
  </section>
</body>
</html>
```